Coral Slumber Depot Website

Need a design for a local CORAL SLUMBER DEPOT store.
The store is called Coral Slumber Depot.
need it to be something that customers can find on the internet and will
give them my location, they need to know i have the same brand mattress as the other store except i have them at almost half the price.

the office phone number is (786)413-9067
the office address is: 24517 sw Heron Glade Ln, Miami FL 33189

included is the logo, id like to stick the with white and teal design

here are is an excerpt that can or cannot be included

"We are a premium mattress discount outlet store located in South Florida; offering Free Delivery to Broward Miami-Dade, the Keys, and Palm Beach.

We carry the best brands in the market: Kellard DreamLoft; Brodin SpineEase, Whitcombe & Lyle, Pardue, among others.

We are open 7 days a week, and we are accessible from all major highways. We are a family business and our goal is to provide you with the most comfortable and best quality mattress at a price that has no competition. Come visit us and take a look at our large inventory selection."

```html
<!DOCTYPE html>
<html lang="en">
<head>
<meta charset="utf-8">
<title>Coral Slumber Depot</title>
<link rel="stylesheet" href="https://fonts.googleapis.com/css2?family=Montserrat:wght@400;600;700&family=Lato:wght@400;700&family=Open+Sans:wght@400;600;700&family=Lora:ital@1&display=swap">
<style>
:root{
  --teal:#0a5a70;
  --teal-dark:#08465a;
  --cyan:#1ab0c8;
  --blue-btn:#1a8fd0;
  --size-blue:#2b4f9e;
  --red:#c1272d;
  --beige:#d5c5a7;
  --page:#f2f2f2;
  --ink:#333;
  --heading:#1d4b5a;
  --footer:#2b2b2b;
  --footer-bottom:#1f1f1f;
  --white:#fff;
}
*{box-sizing:border-box;margin:0;padding:0}
html,body{width:1200px;height:2312px;overflow:hidden}
body{position:relative;background:var(--page);font-family:"Open Sans",Arial,sans-serif;color:var(--ink)}
.abs{position:absolute}

/* hero */
.hero{left:0;top:0;width:1200px;height:683px;background:radial-gradient(ellipse at 50% 45%,#a07a5a 0%,#7a5a42 35%,#4e3a2c 75%,#3a2c22 100%)}
.hero-dim{left:0;top:0;width:1200px;height:683px;background:linear-gradient(180deg,rgba(0,0,0,.15),rgba(0,0,0,0) 30%,rgba(0,0,0,.2))}
.brand{left:125px;top:68px;font-family:"Montserrat",sans-serif;font-size:24px;font-weight:400;color:var(--white);line-height:34px;white-space:nowrap;display:flex;align-items:center;gap:10px}
.brand-mark{width:14px;height:14px;border-radius:50%;background:var(--white);flex:none}
.account{top:18px;font-family:"Montserrat",sans-serif;font-size:18px;color:var(--white)}
.search{left:949px;top:14px;width:120px;height:26px;background:#e8f4f7;border-radius:3px;overflow:hidden;display:flex}
.search span{flex:1;font-size:11px;font-style:italic;color:#6bbfd2;padding:6px 0 0 14px}
.search i{width:28px;background:var(--cyan);display:flex;align-items:center;justify-content:center}
.nav a{position:absolute;top:72px;font-family:"Montserrat",sans-serif;font-size:21px;color:var(--white);text-decoration:none;white-space:nowrap}
.nav a.active{top:67px;left:541px;width:96px;height:39px;background:#dde8ea;color:#4a6a73;text-align:center;line-height:39px;border-radius:2px}
.hero-copy{left:300px;top:456px;width:600px;text-align:center;font-family:"Montserrat",sans-serif;font-size:24px;line-height:30px;color:#eee}
.shop-btn{left:515px;top:566px;width:170px;height:64px;background:var(--cyan);border-radius:5px;color:var(--white);font-family:"Montserrat",sans-serif;font-size:26px;text-align:center;line-height:64px}

/* promo band */
.promo{top:683px;height:207px}
.promo-text{width:303px;background:linear-gradient(180deg,var(--teal) 0%,var(--teal-dark) 100%);padding:22px 22px 22px 28px;color:var(--white);font-family:"Montserrat",sans-serif;font-size:19px;font-weight:600;line-height:25px}
.promo-photo{width:306px}
.read-btn{position:absolute;top:125px;width:143px;height:45px;background:var(--beige);border-radius:4px;color:#333;font-family:"Montserrat",sans-serif;font-size:17px;font-weight:400;text-align:center;line-height:45px}

/* size menu */
.size-menu{left:128px;top:960px;width:275px;background:var(--white);box-shadow:0 1px 3px rgba(0,0,0,.15)}
.size-head{height:48px;background:var(--size-blue);color:var(--white);font-family:"Open Sans",sans-serif;font-size:27px;text-align:center;line-height:48px}
.size-active{height:54px;background:var(--red);color:var(--white);font-size:22px;line-height:54px;padding-left:38px;position:relative}
.size-sub{height:56px;border-bottom:1px solid #ddd;background:linear-gradient(#fff,#f4f4f4);font-size:18px;line-height:56px;text-align:center;color:#333;position:relative}
.size-item{height:48px;border-bottom:1px solid #ddd;color:var(--red);font-size:20px;line-height:52px;padding-left:33px;position:relative}
.size-item:last-child{border-bottom:3px solid var(--red)}
.caret{position:absolute;right:16px;top:50%;margin-top:-3px;width:0;height:0;border-left:6px solid transparent;border-right:6px solid transparent;border-top:6px solid #888}
.size-active .caret{border-top-color:#f2c2c4}
.caret-right{position:absolute;right:20px;top:50%;margin-top:-6px;border-top:6px solid transparent;border-bottom:6px solid transparent;border-left:6px solid #555}

/* products */
.card{width:192px;height:200px;background:var(--beige);border-radius:6px;padding:6px}
.card-photo{height:100px;background:linear-gradient(180deg,#fff 0%,#e9e2d4 55%,#c9b89a 100%);border-radius:2px}
.price{position:absolute;left:66px;top:96px;width:60px;height:26px;background:var(--blue-btn);border:3px solid var(--white);border-radius:5px;color:var(--white);font-size:12px;font-weight:700;text-align:center;line-height:20px}
.card-desc{margin-top:26px;font-size:10px;line-height:12px;color:#9e8f74;text-align:center}
.order-btn{position:absolute;left:52px;top:160px;width:84px;height:30px;background:var(--blue-btn);border-radius:4px;color:var(--white);font-size:13px;text-align:center;line-height:30px}

/* testimonials */
.testi-title{left:0;top:1508px;width:1200px;text-align:center;font-family:"Lato",sans-serif;font-size:29px;font-weight:700;color:var(--heading)}
.quote{width:420px}
.quote-mark{position:absolute;left:0;top:-6px;font-family:Georgia,serif;font-size:74px;line-height:74px;color:var(--heading);font-weight:700}
.quote p{margin-left:48px;font-family:"Lora",serif;font-style:italic;font-size:17px;line-height:20px;color:#333}
.quote .who{margin-top:14px;margin-left:0;text-align:right;padding-right:30px;font-family:"Open Sans",sans-serif;font-style:normal;font-size:13px;color:#555}
.who b{font-weight:400;color:#e05a4a}

/* map */
.map-frame{left:27px;top:1749px;width:1146px;height:270px;background:var(--white);padding:6px;box-shadow:0 1px 4px rgba(0,0,0,.25)}
.map{width:100%;height:100%;background:linear-gradient(135deg,#dfe8c6 0%,#cfe0b4 45%,#e6ecd0 100%)}
.contact-card{left:341px;top:1867px;width:261px;height:117px;background:var(--white);border:1px solid #bbb;box-shadow:0 2px 5px rgba(0,0,0,.3);padding:8px 14px}
.contact-card h3{font-family:"Open Sans",sans-serif;font-size:16px;font-weight:600;color:#e8641c;margin-bottom:6px}
.contact-row{display:flex;gap:10px;align-items:flex-start;font-size:12px;line-height:14px;color:#222;margin-bottom:8px}
.contact-row svg{flex:none}
.map-label{left:691px;top:1898px;height:43px;padding:0 16px;background:#2a2a2a;border-radius:3px;color:var(--white);font-family:"Open Sans",sans-serif;font-size:15px;font-weight:700;white-space:nowrap;line-height:43px}

/* footer */
.footer{left:0;top:2043px;width:1200px;height:237px;background:var(--footer);border-top:6px solid #444}
.footer h4{position:absolute;top:40px;font-size:11px;font-weight:700;color:var(--white)}
.about-text{position:absolute;left:261px;top:64px;width:230px;font-size:8.5px;line-height:14px;color:#ddd}
.about-sign{position:absolute;left:380px;top:148px;font-size:8.5px;color:#ddd}
.social{position:absolute;left:560px;top:64px}
.social li{list-style:none;display:flex;align-items:center;gap:10px;height:29px;font-size:9.5px;color:#ddd}
.social li.hl{color:#3b8de0}
.dot{width:18px;height:18px;border-radius:50%;background:#e5e5e5}
.hl .dot{background:#3b8de0}
.info{position:absolute;left:778px;top:64px}
.info div{display:flex;gap:10px;height:24px;font-size:9.5px;color:#ddd;align-items:center}
.info .ind{padding-left:20px}
.info .mail{color:#3b8de0}
.footer-bottom{left:0;top:2280px;width:1200px;height:32px;background:var(--footer-bottom);font-size:8.5px;color:#ccc;line-height:32px}
</style>
</head>
<body>

<!-- hero -->
<div class="abs hero" role="img" aria-label="Photo of an elegant bedroom with a canopy bed, nightstands and lamps"></div>
<div class="abs hero-dim"></div>
<div class="abs brand"><span class="brand-mark"></span>Coral Slumber Depot</div>
<div class="abs account" style="left:779px">Log in</div>
<div class="abs account" style="left:851px">Register</div>
<div class="abs search"><span>Search item</span><i><svg width="14" height="14" viewBox="0 0 14 14"><circle cx="5.5" cy="5.5" r="4" fill="none" stroke="#fff" stroke-width="2"/><line x1="8.5" y1="8.5" x2="13" y2="13" stroke="#fff" stroke-width="2.5"/></svg></i></div>
<nav class="nav">
  <a class="active" href="#">Home</a>
  <a href="#" style="left:643px">Products</a>
  <a href="#" style="left:760px">Prices</a>
  <a href="#" style="left:846px">About Us</a>
  <a href="#" style="left:966px">Contct Us</a>
</nav>
<div class="abs hero-copy">Lorem ipsum dolor sit amet,<br>consectetur adipiscing elit.<br>Nullam felis mauris</div>
<div class="abs shop-btn">Shop now</div>

<!-- promo band -->
<div class="abs promo promo-text" style="left:0">Aenean ultrices lectus a malesuada consequat. Fusce id malesuada ligula<span class="read-btn" style="left:126px">Read more...</span></div>
<div class="abs promo promo-photo" style="left:303px;background:linear-gradient(180deg,#d9cfc3 0%,#eee6dc 45%,#c0392b 100%)" role="img" aria-label="Photo of a mattress set with orange checked bedding in a bedroom"></div>
<div class="abs promo promo-text" style="left:609px;width:280px">Aenean ultrices lectus a malesuada consequat. Fusce id malesuada ligula<span class="read-btn" style="left:116px">Read more...</span></div>
<div class="abs promo promo-photo" style="left:889px;width:311px;background:linear-gradient(180deg,#e7e3dc 0%,#f3f1ed 50%,#b8b1a6 100%)" role="img" aria-label="Photo of a white quilted mattress on a bed frame"></div>

<!-- size menu -->
<div class="abs size-menu">
  <div class="size-head">SIZE</div>
  <div class="size-active">KING<span class="caret"></span></div>
  <div class="size-sub">Praesent<span class="caret-right"></span></div>
  <div class="size-sub">Venenatis</div>
  <div class="size-sub">Ligula</div>
  <div class="size-item">QUEEN<span class="caret"></span></div>
  <div class="size-item">TWIN<span class="caret"></span></div>
  <div class="size-item">SINGLE<span class="caret"></span></div>
</div>

<!-- product cards -->
<div class="abs card" style="left:570px;top:979px"><div class="card-photo" role="img" aria-label="Photo of a pillow-top mattress"></div><span class="price">$ 124</span><p class="card-desc">Suspendisse et aliquet justo. Duis sed lorem condimentum, leo ac...</p><span class="order-btn">Order now</span></div>
<div class="abs card" style="left:811px;top:979px"><div class="card-photo" role="img" aria-label="Photo of a beige mattress"></div><span class="price">$ 124</span><p class="card-desc">Suspendisse et aliquet justo. Duis sed lorem condimentum, leo ac...</p><span class="order-btn">Order now</span></div>
<div class="abs card" style="left:570px;top:1202px"><div class="card-photo" role="img" aria-label="Photo of a pillow-top mattress"></div><span class="price">$ 124</span><p class="card-desc">Suspendisse et aliquet justo. Duis sed lorem condimentum, leo ac...</p><span class="order-btn">Order now</span></div>
<div class="abs card" style="left:811px;top:1202px"><div class="card-photo" role="img" aria-label="Photo of a beige mattress"></div><span class="price">$ 124</span><p class="card-desc">Suspendisse et aliquet justo. Duis sed lorem condimentum, leo ac...</p><span class="order-btn">Order now</span></div>

<!-- testimonials -->
<h2 class="abs testi-title">Testimonials from our happy customers</h2>
<div class="abs quote" style="left:192px;top:1596px"><span class="quote-mark">“</span><p>Wonderful poducts I will definitely buy again.<br>Thank you so muc Brellwin.</p><p class="who"><b>Noreen Talbott</b>, New York City</p></div>
<div class="abs quote" style="left:632px;top:1596px"><span class="quote-mark">“</span><p>Wonderful poducts I will definitely buy again.<br>Thank you so muc Brellwin.</p><p class="who"><b>Noreen Talbott</b>, New York City</p></div>

<!-- map -->
<div class="abs map-frame"><div class="map" role="img" aria-label="Street map showing the store location near a park"></div></div>
<div class="abs contact-card">
  <h3>Contact Us</h3>
  <div class="contact-row"><svg width="12" height="16" viewBox="0 0 12 16"><path d="M6 0a6 6 0 0 0-6 6c0 4.5 6 10 6 10s6-5.5 6-10a6 6 0 0 0-6-6z" fill="#e8641c"/><circle cx="6" cy="6" r="2.2" fill="#fff"/></svg><span>Lorem Ipsum, Street Name, City<br>Zip Code 12111</span></div>
  <div class="contact-row"><svg width="12" height="14" viewBox="0 0 12 14"><path d="M3 0h3v4H4.5v6H6v4H3C1 14 0 11 0 7s1-7 3-7z" fill="#e8641c"/></svg><span>012-345-6789</span></div>
  <div class="contact-row"><svg width="14" height="10" viewBox="0 0 14 10"><rect width="14" height="10" rx="1" fill="#e8641c"/><path d="M0 1l7 5 7-5" fill="none" stroke="#fff" stroke-width="1.3"/></svg><span>info@coralslumberdepot.com</span></div>
</div>
<svg class="abs" style="left:620px;top:1900px" width="72" height="80" viewBox="0 0 72 80"><path d="M36 2a30 30 0 0 0-30 30c0 22 30 46 30 46s30-24 30-46A30 30 0 0 0 36 2z" fill="#e03a3e"/><circle cx="36" cy="32" r="18" fill="#f6f6f6"/><circle cx="36" cy="32" r="7" fill="#e03a3e"/></svg>
<div class="abs map-label">CORAL SLUMBER DEPOT</div>

<!-- footer -->
<footer class="abs footer">
  <h4 style="left:261px">About Our Company</h4>
  <p class="about-text">Lorem ipsum dolor sit amet, consectetur adipiscing elit. Duis dapibus rhoncus purus, quis aliquet urna vehicula eu. Maecenas velit orci, volutpat sed posuere eu, vehicula eu tellus. Pellentesque sem sapien, aliquet id rhoncus eget, interdum vitae ligula.</p>
  <p class="about-sign">- Gerard Pellman, <b>CEO</b></p>
  <h4 style="left:560px">Keep Connected</h4>
  <ul class="social">
    <li><span class="dot"></span>Like us on Facepage</li>
    <li><span class="dot"></span>Follow us on Chirper</li>
    <li class="hl"><span class="dot"></span>Add us on Circles Plus</li>
    <li><span class="dot"></span>Follow us on Worknet</li>
    <li><span class="dot"></span>Subscribe to our RSS</li>
  </ul>
  <h4 style="left:778px">Contact Information</h4>
  <div class="info">
    <div><svg width="10" height="10" viewBox="0 0 10 10"><path d="M5 0L0 5h1.5v5h2.5V7h2v3h2.5V5H10z" fill="#ddd"/></svg>Delia Ostrow</div>
    <div class="ind">48 Marlow Bend</div>
    <div class="ind">Fernhollow, FH2 7QD</div>
    <div><svg width="10" height="12" viewBox="0 0 10 12"><rect x="2" width="6" height="12" rx="1" fill="#ddd"/></svg>877.5031864</div>
    <div class="mail"><svg width="10" height="8" viewBox="0 0 10 8"><rect width="10" height="8" fill="#ddd"/><path d="M0 0l5 4 5-4" fill="none" stroke="#2b2b2b"/></svg>info@brellwin.ca</div>
  </div>
</footer>
<div class="abs footer-bottom">
  <span class="abs" style="left:261px">Copyright © 2014 Coral Slumber Depot All rights reserved.</span>
  <span class="abs" style="left:673px">Company Information &nbsp;&nbsp; | &nbsp;&nbsp; Privacy Policy &nbsp;&nbsp; | &nbsp;&nbsp; Terms &amp; Conditions</span>
</div>

</body>
</html>
```